Brivolt Technologies business card design

We need a business card designed with our new logo. it would be great if the card could communicate it is a technology based company.

Target Market(s)

system integrators

Industry/Entity Type

technology, IOT

Contact Information for Business Card

Name, designation, Address, telephone number, email address

Requirements
Must have
• logo and company name
Nice to have
• something to do with technology

```html
<!DOCTYPE html>
<html lang="en">
<head>
<meta charset="utf-8">
<title>Brivolt Technologies – Business Card</title>
<link rel="stylesheet" href="https://fonts.googleapis.com/css2?family=Roboto:wght@400;500;700&display=swap">
<style>
  :root {
    --ink: #404042;
    --accent: #f7931e;
    --paper: #ffffff;
    --backdrop: #ffffff;
    --edge: rgba(0,0,0,0.18);
  }
  * { margin: 0; padding: 0; box-sizing: border-box; }
  html, body {
    width: 1200px; height: 896px; overflow: hidden;
    background: var(--backdrop);
    font-family: "Roboto", Arial, sans-serif;
    color: var(--ink);
  }
  .card {
    position: absolute;
    left: 335px; width: 530px; height: 303px;
    background: var(--paper);
    border-radius: 29px;
    box-shadow: 0 2px 6px var(--edge);
  }
  .card--front { top: 125px; }
  .card--back { top: 472px; }

  /* Front */
  .front-brand {
    position: absolute; left: 70px; top: 112px;
    display: flex; align-items: center; gap: 12px;
  }
  .brand-square { width: 26px; height: 26px; background: var(--accent); flex: none; }
  .front-brand .brand-name {
    font-weight: 700; font-size: 24px; line-height: 1.15; color: var(--ink);
  }
  .divider {
    position: absolute; left: 291px; top: 71px;
    width: 2px; height: 163px; background: var(--accent);
  }
  .contact { position: absolute; left: 302px; top: 70px; font-size: 12.5px; line-height: 1; }
  .contact .person-name {
    font-size: 21px; font-weight: 500; color: var(--accent); letter-spacing: 0.2px;
  }
  .contact .role { margin-top: 6px; }
  .contact .address { margin-top: 22px; line-height: 20px; }
  .contact .lines { margin-top: 12px; list-style: none; }
  .contact .lines li { display: flex; align-items: center; gap: 3px; height: 20px; }
  .contact .lines svg { width: 12px; height: 12px; flex: none; }

  /* Back */
  .back-brand {
    position: absolute; left: 40px; top: 96px;
    display: flex; align-items: center; gap: 22px;
  }
  .back-brand .brand-square { width: 84px; height: 84px; }
  .back-brand .brand-name {
    font-weight: 700; font-size: 50px; line-height: 1.05; color: var(--ink);
    letter-spacing: 0.5px;
  }
</style>
</head>
<body>
  <section class="card card--front">
    <div class="front-brand">
      <span class="brand-square"></span>
      <span class="brand-name">Brivolt<br>Technologies</span>
    </div>
    <div class="divider"></div>
    <div class="contact">
      <div class="person-name">DARA KOLVENN</div>
      <div class="role">Managing Director</div>
      <div class="address">4180 Larkmere Quay<br>Fenwick Bay CA 90417</div>
      <ul class="lines">
        <li>
          <svg viewBox="0 0 12 12" aria-hidden="true"><path fill="var(--accent)" d="M2.4 1l2 2.3-1 1.2a6.5 6.5 0 0 0 4.1 4.1l1.2-1 2.3 2-1.2 1.4C5.3 11 1 6.7 1 2.2z"/></svg>
          555 018 264
        </li>
        <li>
          <svg viewBox="0 0 12 12" aria-hidden="true"><rect x="1" y="2.5" width="10" height="7" fill="var(--accent)"/><path d="M1 2.8l5 3.6 5-3.6" stroke="#fff" stroke-width="1" fill="none"/></svg>
          hello@brivolt.example
        </li>
        <li>
          <svg viewBox="0 0 12 12" aria-hidden="true"><circle cx="6" cy="6" r="5" fill="var(--accent)"/><path d="M1 6h10M6 1c-2.5 2.8-2.5 7.2 0 10M6 1c2.5 2.8 2.5 7.2 0 10" stroke="#fff" stroke-width="0.8" fill="none"/></svg>
          www.brivolt.example
        </li>
      </ul>
    </div>
  </section>

  <section class="card card--back">
    <div class="back-brand">
      <span class="brand-square"></span>
      <span class="brand-name">Brivolt<br>Technologies</span>
    </div>
  </section>
</body>
</html>
```